Business Cards for a law firm

Business cards for our law firm. Use our silhoette logo and OAK PARTNERS - check our website (www.oakpartners.example)

Contact Information for Business Card

our silhouette logo, OAK PARTNERS, 800-555-0147, Dorian Pemberton, dorian@oakpartners.example

Requirements
Must have
• our silhouette logo, OAK PARTNERS, 800-555-0147, Dorian Pemberton, dorian@oakpartners.example

```html
<!DOCTYPE html>
<html lang="en">
<head>
<meta charset="utf-8">
<title>Oak Partners – Business Card</title>
<link href="https://fonts.googleapis.com/css2?family=Marcellus+SC&family=Arimo:wght@400&display=swap" rel="stylesheet">
<style>
  :root {
    --navy: #1b2f6e;
    --navy-deep: #14245a;
    --pattern-blue: #2a46a6;
    --white: #ffffff;
    --backdrop: #3a3a3c;
  }
  * { margin: 0; padding: 0; box-sizing: border-box; }
  html, body { width: 1200px; height: 689px; overflow: hidden; }
  body {
    background: var(--backdrop);
    display: flex;
    align-items: center;
    justify-content: center;
    gap: 40px;
  }
  .card {
    position: relative;
    width: 540px;
    height: 310px;
    border-radius: 18px;
    overflow: hidden;
  }
  .card-back {
    background: linear-gradient(135deg, var(--navy-deep), var(--pattern-blue) 60%, var(--navy) 100%);
  }
  .card-front { background: var(--white); }
  .card-front .swoosh-art { position: absolute; inset: 0; }
  .holder-name {
    position: absolute;
    top: 24px;
    right: 48px;
    font-family: "Marcellus SC", serif;
    font-size: 21px;
    letter-spacing: 1px;
    color: var(--navy);
    white-space: nowrap;
  }
  .firm-mark {
    position: absolute;
    left: 44px;
    top: 140px;
    display: flex;
    align-items: center;
    gap: 12px;
  }
  .firm-dot {
    width: 26px;
    height: 26px;
    border-radius: 50%;
    background: var(--navy);
  }
  .firm-name {
    font-family: "Marcellus SC", serif;
    font-size: 30px;
    letter-spacing: 2px;
    color: var(--navy);
    white-space: nowrap;
  }
  .contact-list {
    position: absolute;
    right: 24px;
    top: 196px;
    list-style: none;
    font-family: "Arimo", sans-serif;
    font-size: 13px;
    line-height: 19px;
    color: var(--white);
    text-align: right;
  }
  .contact-list li { display: flex; justify-content: flex-end; align-items: center; gap: 7px; white-space: nowrap; }
  .contact-icon { width: 11px; height: 11px; fill: var(--white); flex: none; }
</style>
</head>
<body>
  <div class="card card-back" role="img" aria-label="Back of card: repeated firm emblem pattern on navy"></div>

  <div class="card card-front">
    <svg class="swoosh-art" viewBox="0 0 540 310" aria-hidden="true">
      <path d="M0,268 C220,264 440,180 530,62 L540,60 L540,310 L0,310 Z" fill="var(--navy)"/>
      <path d="M160,240 C330,206 462,140 512,70 C474,150 342,216 160,240 Z" fill="var(--navy)"/>
    </svg>

    <div class="holder-name">Dorian Pemberton</div>

    <div class="firm-mark">
      <span class="firm-dot"></span>
      <span class="firm-name">OAK PARTNERS</span>
    </div>

    <ul class="contact-list">
      <li>800-555-0147
        <svg class="contact-icon" viewBox="0 0 24 24"><path d="M6.6 10.8a15 15 0 0 0 6.6 6.6l2.2-2.2a1 1 0 0 1 1-.25 11.4 11.4 0 0 0 3.6.57 1 1 0 0 1 1 1V20a1 1 0 0 1-1 1A17 17 0 0 1 3 4a1 1 0 0 1 1-1h3.5a1 1 0 0 1 1 1c0 1.25.2 2.45.57 3.57a1 1 0 0 1-.25 1z"/></svg>
      </li>
      <li>dorian@oakpartners.example
        <svg class="contact-icon" viewBox="0 0 24 24"><path d="M2 5h20v14H2z M4 7v.5l8 5 8-5V7l-8 5z" fill-rule="evenodd"/></svg>
      </li>
      <li>www.oakpartners.example
        <svg class="contact-icon" viewBox="0 0 24 24"><circle cx="12" cy="12" r="10"/></svg>
      </li>
    </ul>
  </div>
</body>
</html>
```